SkyvornQ Business Cards and Stationary Design

Need a design for our business cards and stationary. I want to carry on the theme of the logo. I want the business cards to have a design on the back. I would like the business cards and the stationary to carry the same theme, design scheme, and branding

Target Market(s)

Airlines and Maintenance Facilities

Industry/Entity Type

Aviation

Contact Information for Business Card

Name
Position Title
Address: 4827 Trellis Hollow Road, Fort Pierce, Florida, 34951
Office Number
Mobile Number
Email
Website

Font styles to use
Serif
Sans Serif

Colors

Designer to choose colors to be used in the design.

```html
<!DOCTYPE html>
<html lang="en">
<head>
<meta charset="utf-8">
<title>SkyvornQ Business Cards</title>
<link href="https://fonts.googleapis.com/css2?family=Roboto+Condensed:wght@400;700&family=Roboto:wght@400&display=swap" rel="stylesheet">
<style>
  :root {
    --navy-deep: #0a1f4d;
    --navy: #14336e;
    --blue-mid: #1f5fae;
    --sky: #2ea3e3;
    --paper: #ffffff;
    --paper-soft: #f3f4f6;
    --backdrop: #e9e6e1;
    --ink-grey: #4a4f57;
  }
  * { box-sizing: border-box; margin: 0; padding: 0; }
  html, body { width: 1200px; height: 911px; overflow: hidden; }
  body {
    background: var(--backdrop);
    font-family: "Roboto Condensed", Arial, sans-serif;
    position: relative;
  }
  .card {
    position: absolute;
    width: 560px;
    height: 330px;
    border-radius: 26px;
    overflow: hidden;
    box-shadow: 0 10px 28px rgba(0,0,0,0.18);
  }
  /* Front card */
  .card-front {
    left: 60px;
    top: 110px;
    background: var(--paper);
  }
  .front-panel {
    position: absolute;
    right: 0; top: 0;
    width: 330px; height: 100%;
    background: linear-gradient(135deg, var(--navy) 0%, var(--navy-deep) 100%);
    border-top-left-radius: 200px 330px;
    border-bottom-left-radius: 0;
    padding: 38px 36px 0 0;
    text-align: right;
    color: var(--paper);
  }
  .front-mark {
    position: absolute;
    left: 26px; top: 50px;
    width: 240px; height: 240px;
    border-radius: 50%;
    border: 14px solid var(--blue-mid);
    background: var(--paper);
    display: flex; align-items: center; justify-content: center;
  }
  .front-mark .brand-name {
    font-weight: 700;
    font-size: 34px;
    letter-spacing: 1px;
    color: var(--navy);
  }
  .person-name {
    font-size: 26px;
    font-weight: 400;
    color: var(--sky);
    letter-spacing: 0.5px;
  }
  .person-title {
    font-size: 17px;
    margin-top: 2px;
    letter-spacing: 0.5px;
  }
  .address {
    margin-top: 48px;
    font-size: 15px;
    line-height: 1.35;
  }
  .contact-list {
    list-style: none;
    margin-top: 16px;
    font-size: 15px;
    line-height: 1.45;
  }
  .contact-list li { display: flex; justify-content: flex-end; align-items: center; gap: 8px; }
  .contact-list svg { width: 13px; height: 13px; fill: var(--sky); flex: none; }

  /* Back card */
  .card-back {
    left: 580px;
    top: 470px;
    background: linear-gradient(160deg, var(--paper) 0%, var(--paper-soft) 100%);
    display: flex; flex-direction: column; align-items: center; justify-content: center;
  }
  .back-dot {
    width: 70px; height: 70px;
    border-radius: 50%;
    border: 8px solid var(--blue-mid);
  }
  .back-name {
    margin-top: 18px;
    font-weight: 700;
    font-size: 40px;
    letter-spacing: 6px;
    color: var(--navy-deep);
  }
  .back-web {
    margin-top: 22px;
    font-family: "Roboto", Arial, sans-serif;
    font-size: 13px;
    letter-spacing: 6px;
    color: var(--ink-grey);
  }
</style>
</head>
<body>

<section class="card card-front" aria-label="Business card front">
  <div class="front-mark">
    <span class="brand-name">SkyvornQ</span>
  </div>
  <div class="front-panel">
    <p class="person-name">DANA WHITLOW</p>
    <p class="person-title">CEO/FOUNDER</p>
    <p class="address">4827 Trellis Hollow Road<br>Fort Pierce, Florida, 34951</p>
    <ul class="contact-list">
      <li>772 519 4083
        <svg viewBox="0 0 24 24" aria-hidden="true"><path d="M6.6 10.8a15.1 15.1 0 0 0 6.6 6.6l2.2-2.2c.3-.3.7-.4 1-.2 1.1.4 2.3.6 3.6.6.6 0 1 .4 1 1V20c0 .6-.4 1-1 1C10.6 21 3 13.4 3 4c0-.6.4-1 1-1h3.5c.6 0 1 .4 1 1 0 1.3.2 2.5.6 3.6.1.3 0 .7-.2 1z"/></svg>
      </li>
      <li>772 806 3157
        <svg viewBox="0 0 24 24" aria-hidden="true"><path d="M7 1h10a2 2 0 0 1 2 2v18a2 2 0 0 1-2 2H7a2 2 0 0 1-2-2V3a2 2 0 0 1 2-2zm0 3v14h10V4z"/></svg>
      </li>
      <li>info@skyvornq.com
        <svg viewBox="0 0 24 24" aria-hidden="true"><path d="M2 5h20v14H2zm2 2v.5l8 5 8-5V7l-8 5z"/></svg>
      </li>
      <li>www.skyvornq.com
        <svg viewBox="0 0 24 24" aria-hidden="true"><circle cx="12" cy="12" r="10"/></svg>
      </li>
    </ul>
  </div>
</section>

<section class="card card-back" aria-label="Business card back">
  <div class="back-dot"></div>
  <p class="back-name">SKYVORNQ</p>
  <p class="back-web">www.skyvornq.com</p>
</section>

</body>
</html>
```